New Business Card for Web Design/Internet Marketing Company

Looking for a great looking new business card. We are a 10 year old web design, internet marketing and website management company that works mostly with small businesses.

Our new card needs to better match the colors and style of our website, be bold, extremely usable and slightly edgy.

Target Market(s)

Small/Medium businesses that have websites

Industry/Entity Type

Internet

Requirements
Must have
• Front and back design, full color, rounded corners please

Must use the colors/style of our website (JPG provided)

INFO FOR CARDS (as readable as possible please)
Mark Lenner
President/CEO
mark@trelvanmedia.example
Phone: 520-381-7459
Toll Free: 866-381-7459
Address: 4315 W. Calloway Ave. Ste. 140, Tucson, AZ 85792

THINGS I WANT TO PROMOTE (if there is room):
1. Our Website - www.trelvanmedia.example

2. Social Media
Twitter: @trelvanmedia
Facebook: www.facebook.com/trelvanmedia

3. Our Services
Web Design
Internet Marketing
Website Management

```html
<!DOCTYPE html>
<html lang="en">
<head>
<meta charset="utf-8">
<title>Trelvan Media – Business Card</title>
<link rel="stylesheet" href="https://fonts.googleapis.com/css2?family=Open+Sans:wght@400;600;700&display=swap">
<style>
  :root {
    --orange: #f3822f;
    --blue: #1b8fce;
    --ink: #4a4a4a;
    --rule: #9a9a9a;
    --white: #ffffff;
    --backdrop: #e9e7e4;
  }
  * { margin: 0; padding: 0; box-sizing: border-box; }
  html, body {
    width: 1200px; height: 1129px; overflow: hidden;
    background: var(--backdrop);
    font-family: "Open Sans", Arial, sans-serif;
  }
  .canvas { position: relative; width: 1200px; height: 1129px; }
  .card {
    position: absolute; width: 790px; height: 451px;
    border-radius: 18px; overflow: hidden;
    box-shadow: 0 4px 14px rgba(0,0,0,.18);
  }
  .card-front { left: 78px; top: 90px; background: var(--white); }
  .card-back { left: 311px; top: 597px; background: var(--orange); }

  .brand {
    position: absolute; left: 34px; top: 160px; width: 370px;
    display: flex; align-items: center; justify-content: center; gap: 12px;
  }
  .brand-dot { width: 22px; height: 22px; border-radius: 50%; background: var(--blue); }
  .brand-name { font-size: 44px; font-weight: 700; color: var(--orange); letter-spacing: -0.5px; }

  .divider { position: absolute; left: 429px; top: 92px; width: 1px; height: 206px; background: var(--rule); }

  .contact { position: absolute; left: 460px; top: 108px; color: var(--ink); font-size: 19.5px; }
  .contact-line { display: flex; align-items: center; height: 28.5px; gap: 9px; }
  .contact-line svg { width: 15px; height: 15px; flex: none; }
  .address { margin-top: 22px; line-height: 28px; }

  .bands { position: absolute; left: 0; top: 0; }
  .signature {
    position: absolute; left: 433px; top: 395px; color: var(--white);
    white-space: nowrap;
  }
  .signature-name { font-size: 25px; font-weight: 700; }
  .signature-title { font-size: 20px; font-weight: 400; }

  .back-brand {
    position: absolute; left: 0; top: 110px; width: 100%;
    display: flex; align-items: center; justify-content: center; gap: 16px;
  }
  .back-brand .brand-dot { width: 30px; height: 30px; background: var(--white); }
  .back-brand .brand-name { font-size: 66px; color: var(--white); }

  .services {
    position: absolute; left: 0; width: 100%; top: 290px;
    text-align: center; color: var(--white); font-weight: 700; font-size: 24px; line-height: 34px;
  }
  .services span { margin: 0 10px; }
  .services span::before { content: "\2022"; margin-right: 6px; }

  .social {
    position: absolute; left: 0; width: 100%; top: 375px;
    display: flex; justify-content: center; gap: 26px;
    color: var(--white); font-size: 23px;
  }
  .social-item { display: flex; align-items: center; gap: 8px; }
  .social-mark { width: 20px; height: 20px; background: rgba(255,255,255,.85); border-radius: 3px; }
</style>
</head>
<body>
<div class="canvas">

  <section class="card card-front">
    <div class="brand">
      <span class="brand-dot"></span>
      <span class="brand-name">Trelvan Media</span>
    </div>

    <div class="divider"></div>

    <div class="contact">
      <div class="contact-line">
        <svg viewBox="0 0 16 16"><path d="M4 1 L6.5 4 L5 6 Q6.5 9.5 10 11 L12 9.5 L15 12 L13 15 Q4 14 1 3 Z" fill="none" stroke="#555" stroke-width="1.5"/></svg>
        <span>866-381-7459</span>
      </div>
      <div class="contact-line">
        <svg viewBox="0 0 16 16"><path d="M4 1 L6.5 4 L5 6 Q6.5 9.5 10 11 L12 9.5 L15 12 L13 15 Q4 14 1 3 Z" fill="none" stroke="#555" stroke-width="1.5"/></svg>
        <span>520-381-7459</span>
      </div>
      <div class="contact-line">
        <svg viewBox="0 0 16 16"><rect x="1" y="4" width="14" height="10" fill="none" stroke="#555" stroke-width="1.5"/><path d="M1 4 L8 10 L15 4" fill="none" stroke="#555" stroke-width="1.5"/></svg>
        <span>mark@trelvanmedia.example</span>
      </div>
      <div class="contact-line">
        <svg viewBox="0 0 16 16"><circle cx="8" cy="8" r="7" fill="#555"/><path d="M1 8 H15 M8 1 V15" stroke="#fff" stroke-width="1"/></svg>
        <span>www.trelvanmedia.example</span>
      </div>
      <div class="address">
        4315 W. Calloway Ave. Ste. 140<br>
        Tucson, AZ 85792
      </div>
    </div>

    <svg class="bands" width="790" height="451" viewBox="0 0 790 451">
      <polygon points="0,388 381,388 360,411 0,411" fill="var(--blue)"/>
      <polygon points="393,388 790,388 790,451 0,451 0,424 363,424" fill="var(--orange)"/>
    </svg>

    <div class="signature">
      <span class="signature-name">Mark Lenner ,</span>
      <span class="signature-title">President/CEO</span>
    </div>
  </section>

  <section class="card card-back">
    <div class="back-brand">
      <span class="brand-dot"></span>
      <span class="brand-name">Trelvan Media</span>
    </div>

    <div class="services">
      <div><span>Web Design</span><span>Internet Marketing</span></div>
      <div><span>Website Management</span></div>
    </div>

    <div class="social">
      <div class="social-item"><span class="social-mark"></span><span>@trelvanmedia</span></div>
      <div class="social-item"><span class="social-mark"></span><span>trelvanmedia</span></div>
    </div>
  </section>

</div>
</body>
</html>
```